Redesign specialty cleaning services business brochure

I need a brochure re-designed and updated to reflect packages we sell for starting your own specialty cleaning business. We are a specialty cleaning company that has been in business for over 35 years and our company literature needs an update.The brochure needs to be a downloadable file as well as print-ready.The download will go on 2 of our websites https://brovanco.com/ and http://quietharborbakerysupplyhub.com/. I will attach the brochure that needs to be redesigned. They have not been updated for several years. I have new images to add to the updated brochure.

```html
<!DOCTYPE html>
<html lang="en">
<head>
<meta charset="utf-8">
<title>Window Cleaning Startup Packages</title>
<link rel="stylesheet" href="https://fonts.googleapis.com/css2?family=Bebas+Neue&family=Courgette&family=Open+Sans:wght@400;700&family=Roboto+Condensed:wght@400;700&display=swap">
<style>
  :root{
    --page:#e9e9e7;
    --blue:#1f73c1;
    --sky:#9ac6e6;
    --green:#7cc242;
    --ink:#222;
    --heading:#1d6fbf;
    --white:#fff;
  }
  *{box-sizing:border-box;margin:0;padding:0}
  html,body{width:844px;height:1200px;overflow:hidden;background:var(--page)}
  body{position:relative;font-family:"Open Sans",sans-serif;color:var(--ink)}
  .flyer{position:absolute;left:52px;width:740px;height:574px;background:var(--white);overflow:hidden;box-shadow:0 2px 6px rgba(0,0,0,.18)}
  .flyer--starter{top:17px}
  .flyer--pro{top:609px}
  .flyer__art{position:absolute;inset:0;width:740px;height:574px}
  .flyer__title{position:absolute;left:17px;top:0;height:80px;display:flex;align-items:center;font-family:"Bebas Neue",sans-serif;font-weight:400;font-size:42px;color:var(--white);white-space:nowrap}
  .flyer__title .accent{color:var(--green)}
  .flyer__tagline{position:absolute;left:15px;font-family:"Courgette",cursive;font-size:18px;color:#333}
  .flyer--starter .flyer__tagline{top:96px}
  .flyer--pro .flyer__tagline{top:86px}
  .section{position:absolute;left:17px}
  .section__heading{font-size:12px;font-weight:700;color:var(--heading);text-transform:uppercase;margin-bottom:4px}
  .section__list{list-style:none;font-size:12px}
  .flyer--starter .section__list li{line-height:17px}
  .flyer--pro .section__list li{line-height:15px}
  .section__list li{padding-left:14px;position:relative;white-space:nowrap}
  .section__list li::before{content:"";position:absolute;left:0;top:50%;width:8px;height:8px;margin-top:-4px;border-radius:50%;background:var(--blue)}
  .summary{position:absolute;right:6px;top:478px;text-align:right;color:var(--white)}
  .summary__lead{font-family:"Roboto Condensed",sans-serif;font-weight:700;font-size:15px;line-height:19px;text-transform:uppercase}
  .summary__note{font-size:11.5px;line-height:16px;margin-top:4px}
  .contact{position:absolute;left:15px;top:528px;color:var(--white)}
  .contact__line{display:flex;align-items:center;gap:6px;font-size:14px}
  .contact__web{font-size:12px;margin-top:1px}
  .badge{position:absolute;left:610px;top:340px;width:120px;height:120px;text-align:center;color:var(--white)}
  .badge svg{position:absolute;inset:0}
  .badge__name{position:relative;padding-top:30px;font-family:"Bebas Neue",sans-serif;font-size:21px;line-height:22px}
  .badge__price{position:relative;font-family:"Bebas Neue",sans-serif;font-size:34px;line-height:36px}
</style>
</head>
<body>

<article class="flyer flyer--starter">
  <svg class="flyer__art" viewBox="0 0 740 574" aria-hidden="true">
    <defs>
      <linearGradient id="headStarter" x1="0" y1="0" x2="0" y2="1">
        <stop offset="0" stop-color="#2a86d4"/><stop offset="1" stop-color="#1a62ad"/>
      </linearGradient>
      <linearGradient id="photoStarter" x1="0" y1="0" x2="1" y2="1">
        <stop offset="0" stop-color="#b8b0a3"/><stop offset=".5" stop-color="#8f887d"/><stop offset="1" stop-color="#5b564f"/>
      </linearGradient>
      <linearGradient id="bandStarter" x1="0" y1="0" x2="1" y2="0">
        <stop offset="0" stop-color="#1c64b3"/><stop offset="1" stop-color="#1f79c9"/>
      </linearGradient>
    </defs>
    <rect x="0" y="0" width="740" height="80" fill="url(#headStarter)"/>
    <path d="M445 80 Q320 290 365 574" fill="none" stroke="var(--sky)" stroke-width="14"/>
    <path role="img" aria-label="Photo of a window cleaner on a ladder washing an ornate stone building's window" d="M452 80 Q328 290 372 574 L740 574 L740 80 Z" fill="url(#photoStarter)"/>
    <path d="M0 518 L320 518 L270 574 L0 574 Z" fill="var(--green)"/>
    <path d="M262 574 Q380 466 740 450 L740 574 Z" fill="url(#bandStarter)"/>
  </svg>

  <h1 class="flyer__title">The&nbsp;<span class="accent">KLT</span>&nbsp;Window Cleaning Package for Just&nbsp;<span class="accent">$9,995</span></h1>
  <p class="flyer__tagline">Teaching Glass is Our Task!</p>

  <section class="section" style="top:128px">
    <h2 class="section__heading">Hands-on Window Cleaning Training</h2>
    <ul class="section__list">
      <li>Basic Hands on Window Cleaning Training</li>
      <li>Ladder Safety Traicing Techniques</li>
      <li>Bidding &amp; Estimating Techniques</li>
    </ul>
  </section>
  <section class="section" style="top:220px">
    <h2 class="section__heading">Equipment Includes</h2>
    <ul class="section__list">
      <li>1 omplete Window Cleaning Bucket &amp; Tool Setup</li>
      <li>4 1/2 Sectional Window Cleaning Ladder Set</li>
    </ul>
  </section>
  <section class="section" style="top:288px">
    <h2 class="section__heading">Company Branding Includes</h2>
    <ul class="section__list">
      <li>3 Page Website with 3 Months Free Hosting</li>
      <li>1 Logo Design</li>
      <li>2500 Door Hangers</li>
      <li>2500 Post Cards</li>
      <li>6 Uniform Shirts and Hats with logo</li>
      <li>2 (17.3" x 11.25" Magnetic Vehide Signs</li>
      <li>1 Designed Letterhead , Business Card &amp; Brochure</li>
    </ul>
  </section>
  <section class="section" style="top:444px">
    <h2 class="section__heading">Office Set-up</h2>
    <ul class="section__list">
      <li>20 hours of Business Consulting</li>
      <li>Window Cleaning Marketing &amp; Internet Advertising Plan</li>
    </ul>
  </section>

  <div class="badge">
    <svg viewBox="0 0 120 120" aria-hidden="true">
      <circle cx="60" cy="60" r="52" fill="var(--green)"/>
      <circle cx="60" cy="60" r="55" fill="none" stroke="var(--green)" stroke-width="9" stroke-dasharray="6 4.8"/>
    </svg>
    <div class="badge__name">KLT Package</div>
    <div class="badge__price">$9,995</div>
  </div>

  <div class="summary">
    <p class="summary__lead">The "KLT" Startup Package is a Complete<br>3 Day Window Cleaning System</p>
    <p class="summary__note">Includes Training and Equipment for Just $9,995.00<br>(Training for Up To 2 Team Members)</p>
  </div>

  <div class="contact">
    <p class="contact__line">Call Darlene Voss
      <svg width="14" height="14" viewBox="0 0 14 14" aria-hidden="true"><circle cx="7" cy="7" r="6" fill="none" stroke="#fff" stroke-width="1.3"/><path d="M4.6 4 L5.8 3.8 L6.3 5.3 L5.6 5.9 Q6.3 7.6 8.1 8.4 L8.7 7.7 L10.2 8.2 L10 9.4 Q6.8 9.8 4.6 7 Q4.2 5.5 4.6 4Z" fill="#fff"/></svg>
      877 555 0142</p>
    <p class="contact__web">www.SparkleSillTraining.com</p>
  </div>
</article>

<article class="flyer flyer--pro">
  <svg class="flyer__art" viewBox="0 0 740 574" aria-hidden="true">
    <defs>
      <linearGradient id="headPro" x1="0" y1="0" x2="0" y2="1">
        <stop offset="0" stop-color="#1e4592"/><stop offset="1" stop-color="#122b63"/>
      </linearGradient>
      <linearGradient id="photoPro" x1="0" y1="0" x2="1" y2="1">
        <stop offset="0" stop-color="#a89088"/><stop offset=".5" stop-color="#6c6470"/><stop offset="1" stop-color="#3e4658"/>
      </linearGradient>
      <linearGradient id="bandPro" x1="0" y1="0" x2="1" y2="0">
        <stop offset="0" stop-color="#174a9b"/><stop offset="1" stop-color="#102a64"/>
      </linearGradient>
    </defs>
    <rect x="0" y="0" width="740" height="78" fill="url(#headPro)"/>
    <path d="M445 78 Q320 290 365 574" fill="none" stroke="var(--sky)" stroke-width="14"/>
    <path role="img" aria-label="Photo of a window cleaner on an extension ladder squeegeeing a tall storefront window" d="M452 78 Q328 290 372 574 L740 574 L740 78 Z" fill="url(#photoPro)"/>
    <path d="M0 518 L320 518 L270 574 L0 574 Z" fill="var(--green)"/>
    <path d="M262 574 Q380 466 740 450 L740 574 Z" fill="url(#bandPro)"/>
  </svg>

  <h1 class="flyer__title">The&nbsp;<span class="accent">RVX</span>&nbsp;Window Cleaning Package for Just&nbsp;<span class="accent">$19,995</span></h1>
  <p class="flyer__tagline">Teaching Glass is Our Task!</p>

  <section class="section" style="top:120px">
    <h2 class="section__heading">Hands-on Window Cleaning Training</h2>
    <ul class="section__list">
      <li>Beginning &amp; Advance Window Cleaning Training</li>
      <li>Power Washing Training</li>
      <li>Mini-Blind Cleaning Training</li>
      <li>Ladder Safety Training Techniques</li>
      <li>Bidding &amp; Estimating Techniques</li>
    </ul>
  </section>
  <section class="section" style="top:221px">
    <h2 class="section__heading">Equipment Includes</h2>
    <ul class="section__list">
      <li>1 Complete Window Cleaning Bucket &amp; Tool Setup</li>
      <li>4 1/2 Piece Sectional Window Cleaning Ladder Set</li>
      <li>The ShadeSwift Kit Mobile Mini-Blind Ceaning System</li>
      <li>3 Quick Connect Water Keys</li>
    </ul>
  </section>
  <section class="section" style="top:313px">
    <h2 class="section__heading">Company Branding Includes</h2>
    <ul class="section__list">
      <li>4 Page Website with 6 Months Free Hosting</li>
      <li>1 Logo Design</li>
      <li>5000 Door Hangers</li>
      <li>5000 Post Cards</li>
      <li>12 Uniform Shirts and Hats with Logo</li>
      <li>2 (17,3" x 11.25") Magnetic Vehicle Signs</li>
      <li>1 Designed Letterhead, Business Card &amp; Brochure</li>
    </ul>
  </section>
  <section class="section" style="top:447px">
    <h2 class="section__heading">Office Set-up</h2>
    <ul class="section__list">
      <li>Overview of LedgerLite Software Application</li>
      <li>Overview of Forms Needed for Business Operation</li>
      <li>Window Cleaning Marketing &amp; Internet Advertising Plan</li>
    </ul>
  </section>

  <div class="badge">
    <svg viewBox="0 0 120 120" aria-hidden="true">
      <circle cx="60" cy="60" r="52" fill="var(--green)"/>
      <circle cx="60" cy="60" r="55" fill="none" stroke="var(--green)" stroke-width="9" stroke-dasharray="6 4.8"/>
    </svg>
    <div class="badge__name">RVX Package</div>
    <div class="badge__price">$19,995</div>
  </div>

  <div class="summary">
    <p class="summary__lead">The "RVX" Startup Package is a Complete<br>7 Day Window Cleaning System</p>
    <p class="summary__note">Includes Training and Equipment for Just $19,995.00<br>(Training for Up To 3 Team Members)</p>
  </div>

  <div class="contact">
    <p class="contact__line">Call Darlene Voss
      <svg width="14" height="14" viewBox="0 0 14 14" aria-hidden="true"><circle cx="7" cy="7" r="6" fill="none" stroke="#fff" stroke-width="1.3"/><path d="M4.6 4 L5.8 3.8 L6.3 5.3 L5.6 5.9 Q6.3 7.6 8.1 8.4 L8.7 7.7 L10.2 8.2 L10 9.4 Q6.8 9.8 4.6 7 Q4.2 5.5 4.6 4Z" fill="#fff"/></svg>
      877 555 0142</p>
    <p class="contact__web">www.SparkleSillTraining.com</p>
  </div>
</article>

</body>
</html>
```